Modern Verdell Tree Care Website

I need a website for a full service Tree Care company. The company provides tree pruning, tree removal, tree preservation, emergency services, stump grinding, and emergency tree services.

Target Market(s)

Customers that need tree services

Industry/Entity Type

Landscaping, Tree Services

Coding

Coded - Design and coding required

Number of Pages Required

5+ page

Font styles to use
Sans Serif

Requirements
Must have
• Good clean design that showcases the services the company provides.
Nice to have
• Services page; contact form, blog, home page, about page

```html
<!DOCTYPE html>
<html lang="en">
<head>
<meta charset="UTF-8">
<title>Verdell Tree Care</title>
<link href="https://fonts.googleapis.com/css2?family=Plus+Jakarta+Sans:wght@400;500;600;700;800&display=swap" rel="stylesheet">
<style>
:root{
  --forest:#2c5222;
  --forest-deep:#1d4212;
  --button:#2a5a1d;
  --white:#ffffff;
  --paper:#ececec;
  --ink:#121212;
  --card:#eef0f6;
  --body-ink:#333;
  --photo-dark:#3b4a2a;
  --photo-orange:#b8612a;
  --photo-moss:#5d6a3a;
}
*{margin:0;padding:0;box-sizing:border-box}
html,body{width:1200px;height:4402px;overflow:hidden}
body{font-family:"Plus Jakarta Sans",Arial,sans-serif;color:var(--white);position:relative;background:var(--white)}
.abs{position:absolute}
.photo{position:absolute}
.btn{position:absolute;display:flex;align-items:center;justify-content:center;font-size:15px;font-weight:600;letter-spacing:.2px;text-transform:uppercase}
.btn-solid{background:var(--button);color:var(--white)}
.btn-outline{border:3px solid var(--white);color:var(--white)}
.btn-white{background:var(--white);color:var(--forest-deep)}
.btn-green-outline{border:3px solid var(--button);color:var(--button)}
.rule{position:absolute;height:6px;background:var(--white)}

/* hero */
.hero{position:absolute;left:0;top:0;width:1200px;height:732px;overflow:hidden}
.hero .photo{inset:0;background:linear-gradient(120deg,#2f3a22 0%,#4c5631 35%,#7a5a2e 60%,#3d4a27 80%,#2b3520 100%)}
.hero .shade{position:absolute;inset:0;background:rgba(20,30,15,.35)}
.logo{position:absolute;display:flex;align-items:center;gap:14px;font-weight:800;font-size:30px;letter-spacing:1px;color:var(--white)}
.logo .mark{width:38px;height:38px;background:#7fb540}
.nav{position:absolute;left:441px;top:34px;display:flex;gap:22px;font-size:17px;font-weight:500}
.hero .eyebrow{left:101px;top:190px;font-size:36px;font-weight:500;display:flex;align-items:center;gap:14px}
.hero .eyebrow span.line{width:100px;height:3px;background:var(--white);display:block}
.hero h1{left:101px;top:250px;font-size:82px;font-weight:700;line-height:100px;letter-spacing:-1px}
.hero .sub{left:101px;top:455px;font-size:31px;font-weight:400}

/* who */
.who{position:absolute;left:0;top:732px;width:1200px;height:833px}
.who .panel{position:absolute;left:0;top:0;width:600px;height:833px;background:var(--forest)}
.who .photo{left:600px;top:0;width:600px;height:833px;background:linear-gradient(160deg,#6f7a48 0%,#9a6a35 40%,#c8702e 55%,#4d5a2c 80%,#3a4322 100%)}
h2{position:absolute;font-size:48px;font-weight:700;letter-spacing:-.5px}
.copy{position:absolute;font-size:19px;line-height:33px;font-weight:400}

/* why */
.why{position:absolute;left:0;top:1565px;width:1200px;height:833px}
.why .photo{left:0;top:0;width:600px;height:833px;background:linear-gradient(200deg,#556236 0%,#6d5a34 35%,#c0682c 50%,#7b5c36 70%,#48522b 100%)}
.why .panel{position:absolute;left:600px;top:0;width:600px;height:833px;background:linear-gradient(135deg,#f1f1f1,#e2e2e2)}
.why h2,.why .copy{color:var(--ink)}
.ticks{position:absolute;left:673px;top:1955px;list-style:none;color:var(--ink);font-size:20px}
.ticks li{height:38.5px;display:flex;align-items:center;gap:18px}

/* services */
.services{position:absolute;left:0;top:2398px;width:1200px;height:998px;background:var(--forest)}
.services h2{left:0;width:1200px;text-align:center;top:135px}
.card{position:absolute;width:187px;height:217px;background:var(--card);color:var(--body-ink);text-align:center}
.card .icon{position:absolute;left:54px;top:-40px;width:79px;height:80px;background:var(--button);display:flex;align-items:center;justify-content:center}
.card h3{position:absolute;left:0;width:187px;top:46px;font-size:19px;line-height:24px;font-weight:700;color:#2f3f2a}
.card h3::after{content:"";display:block;width:100px;height:2px;background:#6a8a5c;margin:3px auto 0}
.card p{position:absolute;left:14px;width:159px;top:115px;font-size:12.5px;line-height:20px}

/* cta */
.cta{position:absolute;left:0;top:3396px;width:1200px;height:535px;overflow:hidden}
.cta .photo{inset:0;background:linear-gradient(100deg,#3f4e2a 0%,#c27a2c 30%,#5b6a3a 55%,#a0502c 75%,#3b4726 100%)}
.cta .box{position:absolute;left:185px;top:102px;width:828px;height:330px;background:rgba(44,82,34,.82)}
.cta h2{left:0;width:828px;text-align:center;top:42px}
.cta .lead{position:absolute;left:0;width:828px;text-align:center;top:156px;font-size:19px;line-height:24px}

/* footer */
.footer{position:absolute;left:0;top:3931px;width:1200px;height:471px;background:var(--forest-deep)}
.footer h4{position:absolute;font-size:24px;font-weight:700}
.footer .small{position:absolute;font-size:16px;line-height:29px}
.contact-line{position:absolute;left:465px;display:flex;align-items:center;gap:10px;font-size:16px}
.social{position:absolute;left:465px;top:330px;display:flex;gap:14px}
.social span{width:26px;height:26px;background:var(--white)}
.subscribe{position:absolute;left:820px;top:215px;display:flex;height:36px}
.subscribe .field{width:228px;background:var(--white);color:#999;font-size:13px;display:flex;align-items:center;padding-left:10px}
.subscribe .go{width:84px;background:var(--button);font-size:13px;font-weight:600;display:flex;align-items:center;justify-content:center}
.footer .divider{position:absolute;left:67px;top:396px;width:1065px;height:3px;background:var(--white)}
.footer .copyright{position:absolute;left:67px;top:412px;font-size:11px}
</style>
</head>
<body>

<section class="hero">
  <div class="photo" role="img" aria-label="Arborist in orange safety gear cutting a fallen tree trunk with a chainsaw in a forest"></div>
  <div class="shade"></div>
  <div class="logo" style="left:65px;top:24px"><span class="mark"></span>VERDELL TREE CARE</div>
  <nav class="nav"><span>HOME</span><span>SERVICES</span><span>BLOG</span><span>ABOUT</span><span>CONTACT</span></nav>
  <div class="btn btn-outline" style="left:980px;top:26px;width:152px;height:39px;font-size:13px">Contact Us</div>
  <div class="abs eyebrow">WELCOME TO VERDELL TREE CARE <span class="line"></span></div>
  <h1 class="abs">For All Your Tree<br>Care Needs</h1>
  <p class="abs sub">We are More Than Just a Tree Service Company</p>
  <div class="btn btn-solid" style="left:101px;top:511px;width:232px;height:44px">Contact Us</div>
  <div class="btn btn-outline" style="left:347px;top:511px;width:231px;height:44px">Learn More</div>
</section>

<section class="who">
  <div class="panel"></div>
  <div class="photo" role="img" aria-label="Arborist in orange helmet and jacket operating a chainsaw at the base of a tree"></div>
  <h2 style="left:101px;top:108px">WHO WE ARE?</h2>
  <div class="rule" style="left:101px;top:197px;width:265px"></div>
  <p class="copy" style="left:101px;top:240px;width:420px">At Verdell Tree Care, we are more than just a tree service company, we are stewards of our beautiful trees. With a passion deeply rooted in arboriculture, we embark on a mission to promote the health, beauty, and safety of your trees and landscapes.</p>
  <p class="copy" style="left:101px;top:456px;width:420px">Wheter it's expert tree trimming to enhance aesthetics, meticulous tree removal to mitigate hazards, or comprehensive tree health assessments to ensure safety, we approach each task with unwavering dedication and attention to detail.</p>
  <div class="btn btn-white" style="left:101px;top:688px;width:164px;height:45px;font-size:13px">Contact Us</div>
  <div class="btn btn-outline" style="left:289px;top:688px;width:166px;height:45px;font-size:13px">Learn More</div>
</section>

<section class="why">
  <div class="photo" role="img" aria-label="Arborist in orange gear with a chainsaw standing among felled branches on a forest slope"></div>
  <div class="panel"></div>
  <h2 style="left:673px;top:124px">WHY CHOOSE US?</h2>
  <div class="rule" style="left:673px;top:218px;width:265px;background:var(--button)"></div>
  <p class="copy" style="left:673px;top:258px;width:450px;font-size:20px">At Verdell Tree Care, we are more than just a tree service company, we are stewards of our beautiful trees.</p>
  <div class="btn btn-solid" style="left:673px;top:681px;width:165px;height:43px;font-size:13px">Contact Us</div>
  <div class="btn btn-green-outline" style="left:863px;top:681px;width:164px;height:43px;font-size:13px">Learn More</div>
</section>
<ul class="ticks">
  <li><svg width="22" height="20" viewBox="0 0 22 20"><polyline points="2,11 8,17 20,3" fill="none" stroke="#121212" stroke-width="2.5"/></svg>Licensed and Insured</li>
  <li><svg width="22" height="20" viewBox="0 0 22 20"><polyline points="2,11 8,17 20,3" fill="none" stroke="#121212" stroke-width="2.5"/></svg>24–Hours Emergency Services</li>
  <li><svg width="22" height="20" viewBox="0 0 22 20"><polyline points="2,11 8,17 20,3" fill="none" stroke="#121212" stroke-width="2.5"/></svg>Locally Owned &amp; Operated</li>
  <li><svg width="22" height="20" viewBox="0 0 22 20"><polyline points="2,11 8,17 20,3" fill="none" stroke="#121212" stroke-width="2.5"/></svg>Professional Work</li>
  <li><svg width="22" height="20" viewBox="0 0 22 20"><polyline points="2,11 8,17 20,3" fill="none" stroke="#121212" stroke-width="2.5"/></svg>Safety is Our Priority</li>
  <li><svg width="22" height="20" viewBox="0 0 22 20"><polyline points="2,11 8,17 20,3" fill="none" stroke="#121212" stroke-width="2.5"/></svg>Free Estimates</li>
  <li><svg width="22" height="20" viewBox="0 0 22 20"><polyline points="2,11 8,17 20,3" fill="none" stroke="#121212" stroke-width="2.5"/></svg>Licensed Arborist on Staff</li>
</ul>

<section class="services">
  <h2>WHAT WE CAN DO FOR YOU</h2>
  <div class="rule" style="left:465px;top:216px;width:267px"></div>

  <div class="card" style="left:67px;top:302px"><div class="icon"><svg width="44" height="44" viewBox="0 0 44 44" fill="none" stroke="#fff" stroke-width="3"><circle cx="13" cy="33" r="6"/><circle cx="31" cy="33" r="6"/><line x1="17" y1="28" x2="34" y2="5"/><line x1="27" y1="28" x2="10" y2="5"/></svg></div><h3>Tree<br>Trimming</h3><p>Lorem ipsum dolor sit amet consectetur. Sit aenean sed ullamcorper nulla at.</p></div>
  <div class="card" style="left:285px;top:302px"><div class="icon"><svg width="44" height="44" viewBox="0 0 44 44" fill="#fff"><rect x="20" y="6" width="16" height="14" rx="2"/><rect x="8" y="18" width="5" height="24" transform="rotate(40 10 30)"/></svg></div><h3>Tree<br>Removal</h3><p>Lorem ipsum dolor sit amet consectetur. Sit aenean sed ullamcorper nulla at.</p></div>
  <div class="card" style="left:506px;top:302px"><div class="icon"><svg width="44" height="44" viewBox="0 0 44 44" fill="#fff"><rect x="6" y="10" width="18" height="16" rx="2"/><rect x="4" y="28" width="28" height="10" rx="5"/><rect x="34" y="16" width="4" height="22"/></svg></div><h3>Tree<br>Clearing</h3><p>Lorem ipsum dolor sit amet consectetur. Sit aenean sed ullamcorper nulla at.</p></div>
  <div class="card" style="left:726px;top:302px"><div class="icon"><svg width="44" height="44" viewBox="0 0 44 44" fill="#fff"><path d="M34 4 L40 10 L16 34 L8 36 L10 28 Z"/></svg></div><h3>Tree<br>Pruning</h3><p>Lorem ipsum dolor sit amet consectetur. Sit aenean sed ullamcorper nulla at.</p></div>
  <div class="card" style="left:945px;top:302px"><div class="icon"><svg width="44" height="44" viewBox="0 0 44 44" fill="#fff"><rect x="8" y="8" width="22" height="16" rx="2"/><circle cx="12" cy="32" r="6"/><circle cx="32" cy="32" r="6"/></svg></div><h3>Stump<br>Grinding</h3><p>Lorem ipsum dolor sit amet consectetur. Sit aenean sed ullamcorper nulla at.</p></div>

  <div class="card" style="left:176px;top:629px"><div class="icon"><svg width="44" height="44" viewBox="0 0 44 44" fill="#fff"><rect x="8" y="8" width="22" height="16" rx="2"/><circle cx="12" cy="32" r="6"/><circle cx="32" cy="32" r="6"/></svg></div><h3>Tree<br>Preservation</h3><p>Lorem ipsum dolor sit amet consectetur. Sit aenean sed ullamcorper nulla at.</p></div>
  <div class="card" style="left:395px;top:629px"><div class="icon"><svg width="44" height="44" viewBox="0 0 44 44" fill="#fff"><rect x="8" y="8" width="22" height="16" rx="2"/><circle cx="12" cy="32" r="6"/><circle cx="32" cy="32" r="6"/></svg></div><h3>Storm Damage<br>Clean Up</h3><p>Lorem ipsum dolor sit amet consectetur. Sit aenean sed ullamcorper nulla at.</p></div>
  <div class="card" style="left:615px;top:629px"><div class="icon"><svg width="48" height="44" viewBox="0 0 48 44"><path d="M24 3 L46 41 L2 41 Z" fill="#fff"/><rect x="22" y="15" width="4" height="14" fill="#2a5a1d"/><rect x="22" y="32" width="4" height="4" fill="#2a5a1d"/></svg></div><h3>Emergency<br>Tree Services</h3><p>Lorem ipsum dolor sit amet consectetur. Sit aenean sed ullamcorper nulla at.</p></div>
  <div class="card" style="left:834px;top:629px"><div class="icon"><svg width="44" height="44" viewBox="0 0 44 44" fill="none" stroke="#fff" stroke-width="4"><circle cx="30" cy="12" r="6"/><line x1="26" y1="17" x2="8" y2="38"/></svg></div><h3>Cabling &amp;<br>Bracing</h3><p>Lorem ipsum dolor sit amet consectetur. Sit aenean sed ullamcorper nulla at.</p></div>
</section>

<section class="cta">
  <div class="photo" role="img" aria-label="Arborist in orange jacket and red helmet working among pine trees"></div>
  <div class="box">
    <h2>DO YOU NEED TREE CARE?</h2>
    <div class="rule" style="left:288px;top:122px;width:265px"></div>
    <p class="lead">Call us now to see how we can help you with all of your tree<br>needs</p>
    <div class="btn btn-outline" style="left:155px;top:231px;width:250px;height:43px">Contact Us</div>
    <div class="btn btn-outline" style="left:423px;top:231px;width:250px;height:43px">Learn More</div>
  </div>
</section>

<footer class="footer">
  <div class="logo" style="left:75px;top:70px;font-size:30px"><span class="mark" style="background:#fff"></span>VERDELL TREE CARE</div>
  <p class="small" style="left:75px;top:165px;width:320px">Verdell Tree Care, we are more than just a tree service company, we are stewards of our beautiful trees. With a passion deeply rooted in arboriculture, we embark on a mission to promote the health, beauty, and safety of your trees and landscapes.</p>

  <h4 style="left:465px;top:110px">Contact Verdell Tree Care</h4>
  <p class="small" style="left:465px;top:157px;width:280px;line-height:25px">Serving Brookhaven and surronding areas</p>
  <div class="contact-line" style="top:226px"><svg width="18" height="18" viewBox="0 0 24 24" fill="#fff"><path d="M6.6 10.8a15 15 0 0 0 6.6 6.6l2.2-2.2a1 1 0 0 1 1-.25 11.4 11.4 0 0 0 3.6.57 1 1 0 0 1 1 1V20a1 1 0 0 1-1 1A17 17 0 0 1 3 4a1 1 0 0 1 1-1h3.5a1 1 0 0 1 1 1c0 1.25.2 2.45.57 3.6a1 1 0 0 1-.25 1z"/></svg>(555) 214–7730</div>
  <div class="contact-line" style="top:264px"><svg width="18" height="18" viewBox="0 0 24 24" fill="#fff"><path d="M6.6 10.8a15 15 0 0 0 6.6 6.6l2.2-2.2a1 1 0 0 1 1-.25 11.4 11.4 0 0 0 3.6.57 1 1 0 0 1 1 1V20a1 1 0 0 1-1 1A17 17 0 0 1 3 4a1 1 0 0 1 1-1h3.5a1 1 0 0 1 1 1c0 1.25.2 2.45.57 3.6a1 1 0 0 1-.25 1z"/></svg>(555) 309–4418</div>
  <div class="social"><span></span><span></span><span></span></div>

  <h4 style="left:820px;top:110px">Subscribe</h4>
  <p class="small" style="left:820px;top:147px;width:320px;line-height:25px">Enter your email address to register to our newsletter subscription</p>
  <div class="subscribe"><div class="field">Enter e-mail address</div><div class="go">Subscribe</div></div>

  <div class="divider"></div>
  <p class="copyright">© 2024 Verdell Tree Care. All rights reserved.</p>
</footer>

</body>
</html>
```